Net Wyre Business banner needed

The image size is 1128 px X 191 px

This is a NetWyre Company Banner. Pellam Hire Co is the company and I have attached our logo. We are an advance staffing company that only recruits sales professionals.

```html
<!DOCTYPE html>
<html lang="en">
<head>
<meta charset="utf-8">
<title>Pellam Hire Co — Sales Recruiting Banner</title>
<link rel="stylesheet" href="https://fonts.googleapis.com/css2?family=Roboto+Condensed:wght@400;500;700&display=swap">
<style>
  :root {
    --stage-blue: #002d6e;
    --concrete-light: #e2e2e2;
    --concrete-mid: #cdcdcd;
    --concrete-dark: #b4b4b4;
    --navy-text: #24305a;
    --accent-blue: #1b87c6;
    --brand-blue: #2d4f8e;
    --portrait-sky: #c6ccd3;
    --portrait-skin: #b08c78;
    --portrait-navy: #1f2a3f;
  }
  * { margin: 0; padding: 0; box-sizing: border-box; }
  html, body {
    width: 1200px;
    height: 494px;
    overflow: hidden;
    background: var(--stage-blue);
  }
  .canvas {
    position: relative;
    width: 1200px;
    height: 494px;
    background: var(--stage-blue);
  }
  .banner {
    position: absolute;
    left: 190px;
    top: 179px;
    width: 822px;
    height: 139px;
    overflow: hidden;
    background: radial-gradient(ellipse at 35% 35%, var(--concrete-light) 0%, var(--concrete-mid) 60%, var(--concrete-dark) 100%);
    font-family: "Roboto Condensed", "Arial Narrow", sans-serif;
  }
  .brand {
    position: absolute;
    left: 44px;
    top: 58px;
    width: 176px;
  }
  .brand-name {
    display: flex;
    align-items: center;
    gap: 7px;
    font-size: 24px;
    font-weight: 400;
    letter-spacing: 1px;
    color: var(--brand-blue);
    line-height: 1;
    white-space: nowrap;
  }
  .brand-mark {
    width: 8px;
    height: 8px;
    background: var(--brand-blue);
  }
  .brand-tagline {
    margin-top: 5px;
    text-align: right;
    padding-right: 6px;
    font-size: 6px;
    letter-spacing: 0.9px;
    color: var(--brand-blue);
    white-space: nowrap;
  }
  .headline {
    position: absolute;
    left: 262px;
    top: 50px;
    text-transform: uppercase;
    font-size: 19px;
    line-height: 21px;
    letter-spacing: 0.7px;
    white-space: nowrap;
  }
  .headline-lead {
    display: block;
    font-weight: 400;
    color: var(--navy-text);
  }
  .headline-emphasis {
    display: block;
    font-weight: 700;
    color: var(--accent-blue);
  }
  .portrait {
    position: absolute;
    right: 0;
    top: 0;
    width: 142px;
    height: 139px;
    background:
      radial-gradient(ellipse 38% 34% at 50% 40%, var(--portrait-skin) 0%, rgba(176,140,120,0) 100%),
      linear-gradient(180deg, var(--portrait-sky) 0%, #a9b0b9 50%, var(--portrait-navy) 100%);
  }
</style>
</head>
<body>
  <main class="canvas">
    <section class="banner">
      <div class="brand">
        <div class="brand-name">Pellam Hire Co<span class="brand-mark"></span></div>
        <div class="brand-tagline">YOUR A.I SALES RECRUITER</div>
      </div>

      <h1 class="headline">
        <span class="headline-lead">We are an advance staffing company</span>
        <span class="headline-emphasis">that only recruits sales professionals.</span>
      </h1>

      <div class="portrait" role="img" aria-label="Portrait photo of the company's smiling recruiter in a dark blazer and white shirt"></div>
    </section>
  </main>
</body>
</html>
```